Redesign of Form/Document Navigation Page

I need a redesign of our document and navigation bar on the left. We want the same navigation bar layout/setup but want the buttons and typography to be simple and matching all over. The form needs to be aesthetically pleasing and fit within the page.

1st attachment is our Direct Deposit and the second is the form continued.

```html
<!DOCTYPE html>
<html lang="en">
<head>
<meta charset="utf-8">
<title>Direct Deposit – Northgate Watch</title>
<link href="https://fonts.googleapis.com/css2?family=Open+Sans:wght@400;600;700&display=swap" rel="stylesheet">
<style>
  :root {
    --navy: #26235c;
    --gold: #ebb022;
    --link: #5a5592;
    --panel: #f4f4f4;
    --band: #ebebeb;
    --line: #cfcfcf;
    --text: #222;
    --muted: #777;
    --white: #fff;
  }
  * { box-sizing: border-box; margin: 0; padding: 0; }
  html, body { width: 1200px; height: 826px; overflow: hidden; }
  body { position: relative; background: var(--white); font-family: "Open Sans", Arial, sans-serif; color: var(--text); }

  .site-header { position: absolute; left: 0; top: 0; width: 1200px; height: 110px; }
  .brand { position: absolute; left: 132px; top: 38px; display: flex; align-items: center; gap: 10px; }
  .brand-mark { width: 30px; height: 30px; background: var(--navy); }
  .brand-name { font-weight: 600; color: var(--navy); font-size: 24px; line-height: 30px; }
  .top-nav { position: absolute; top: 46px; left: 828px; display: flex; align-items: center; font-size: 12px; }
  .top-nav a { color: var(--link); text-decoration: none; display: flex; align-items: center; gap: 3px; margin-right: 18px; }
  .top-nav a svg { width: 11px; height: 11px; fill: var(--link); }
  .user { display: flex; align-items: center; gap: 7px; margin-left: 12px; color: var(--text); font-size: 12px; }
  .avatar { width: 36px; height: 36px; border-radius: 50%; background: linear-gradient(135deg, #d9b08c, #8a6a55); }

  .sub-bar { position: absolute; left: 0; top: 110px; width: 1200px; height: 40px; background: var(--band); }
  .back-btn { position: absolute; left: 132px; top: 0; width: 112px; height: 40px; background: var(--navy); color: var(--white); font-size: 12px; display: flex; align-items: center; justify-content: center; gap: 5px; }
  .back-btn svg { width: 9px; height: 9px; }

  .side-nav { position: absolute; left: 132px; top: 170px; width: 240px; }
  .nav-item { position: relative; height: 80px; margin-bottom: 2.4px; background: var(--navy); color: var(--white); display: flex; align-items: center; padding-left: 22px; font-size: 15px; }
  .nav-item svg { width: 26px; height: 24px; margin-right: 14px; fill: none; stroke: var(--white); stroke-width: 2; }
  .nav-item.active { background: var(--gold); }
  .nav-item.active::after { content: ""; position: absolute; right: -14px; top: 30px; border-left: 14px solid var(--gold); border-top: 10px solid transparent; border-bottom: 10px solid transparent; }

  .form-panel { position: absolute; left: 376px; top: 170px; width: 691px; height: 574px; background: var(--panel); }
  .scroll-track { position: absolute; left: 680px; top: 8px; width: 4px; height: 558px; background: #e2e2e2; }
  .scroll-thumb { position: absolute; left: 679px; top: 352px; width: 5px; height: 80px; background: var(--navy); }

  .field { position: absolute; }
  .field label { display: block; font-size: 15px; color: var(--text); margin-bottom: 5px; }
  .input { width: 192px; height: 40px; background: var(--white); border: 1px solid var(--line); position: relative; font-size: 12px; color: var(--muted); display: flex; align-items: center; justify-content: space-between; padding: 0 15px; }
  .input.tall { height: 48px; }
  .radio { position: absolute; top: 147px; display: flex; align-items: center; gap: 5px; font-size: 15px; }
  .radio span { width: 12px; height: 12px; border: 1px solid #888; border-radius: 50%; background: var(--white); }

  .notice { position: absolute; left: 32px; top: 220px; width: 628px; height: 216px; background: var(--white); border: 1px solid var(--line); padding: 20px 20px 0 21px; }
  .notice h2 { font-weight: 400; font-size: 14.5px; color: var(--navy); margin-bottom: 9px; }
  .notice p { font-size: 11.5px; line-height: 19.2px; color: var(--muted); text-align: justify; }

  .site-footer { position: absolute; left: 0; top: 770px; width: 1200px; height: 56px; background: var(--band); font-size: 12px; text-align: center; line-height: 56px; color: var(--text); }
</style>
</head>
<body>
  <header class="site-header">
    <div class="brand"><span class="brand-mark"></span><span class="brand-name">Northgate Watch</span></div>
    <nav class="top-nav">
      <a href="#"><svg viewBox="0 0 10 10"><path d="M5 0 0 5h1.5v5h2.5V7h2v3h2.5V5H10z"/></svg>Home</a>
      <a href="#"><svg viewBox="0 0 10 10"><circle cx="5" cy="5" r="4" fill="none" stroke="#5a5592" stroke-width="2"/></svg>Help</a>
      <div class="user"><span class="avatar" role="img" aria-label="User profile photo"></span>Dana Whitley</div>
    </nav>
  </header>

  <div class="sub-bar">
    <div class="back-btn"><svg viewBox="0 0 10 10" fill="none" stroke="#fff" stroke-width="1.6"><path d="M5 1 1 5l4 4M9 1 5 5l4 4"/></svg>Back To Profile</div>
  </div>

  <nav class="side-nav">
    <div class="nav-item active"><svg viewBox="0 0 26 24"><rect x="1" y="5" width="24" height="14" rx="1"/><circle cx="13" cy="12" r="4"/></svg>Direct Deposit</div>
    <div class="nav-item"><svg viewBox="0 0 26 24"><path d="M6 1h10l5 5v17H6z"/><path d="M10 12h7M10 16h7M10 20h7"/></svg>Change W-4</div>
    <div class="nav-item"><svg viewBox="0 0 26 24"><path d="M2 12h12M10 7l5 5-5 5"/><path d="M15 3h7v18h-7"/></svg>Labour Code</div>
    <div class="nav-item"><svg viewBox="0 0 26 24"><circle cx="13" cy="12" r="10" fill="#fff"/><path d="M13 6v8M13 16v2" stroke="#26235c" stroke-width="2.5"/></svg>Personal Information</div>
    <div class="nav-item"><svg viewBox="0 0 26 24"><rect x="2" y="6" width="22" height="16" rx="2"/><path d="M9 6V3h8v3M13 10v8M9 14h8"/></svg>Appraisal and Review</div>
    <div class="nav-item"><svg viewBox="0 0 26 24"><path d="M3 8h8v14H3zM11 12h8v-10h-6l-2 2"/><path d="M11 12v10h10V12z"/></svg>Write Up-Slip</div>
    <div class="nav-item"><svg viewBox="0 0 26 24"><path d="M1 2v21h24"/><path d="M6 20v-6M10 20v-9M14 20v-7M18 20v-11"/></svg>Employee Performance</div>
  </nav>

  <main class="form-panel">
    <div class="scroll-track"></div><div class="scroll-thumb"></div>

    <div class="field" style="left:30px;top:31px"><label>Routing Transit Number</label><div class="input"></div></div>
    <div class="field" style="left:250px;top:31px"><label>Account Number</label><div class="input"></div></div>

    <div class="radio" style="left:31px"><span></span>Checking</div>
    <div class="radio" style="left:155px"><span></span>Savings</div>
    <div class="field" style="left:250px;top:118px"><label>Amount</label><div class="input">100<span>%</span></div></div>

    <section class="notice">
      <h2>IMPORTANT! Please read and sign before completing and submitting.</h2>
      <p>I hereby authorize NORTHGATE WATCH to deposit any amounts owed me, as instructed by my employer, by initiating credit entries to my account at the financial institution (hereinafter "Bank") indicated on this form. Further, I authorize Bank to accept and to credit any credit entries indicated by NORTHGATE WATCH to my account In the even that NORTHGATE WATCH deposits funds erroneously into my account, I authorize NORTHGATE WATCH to debit my account for an amount not to exceed the original amount of the erroneous credit This authorization is to remain in . force and effect until NORTHGATE WATCH and Bank have received written notice from me of its termination in such time and in such manner as to afford NORTHGATE WATCH and Bank reasonable opportunity to act on it</p>
    </section>

    <div class="field" style="left:30px;top:472px"><label>Employee Name :</label><div class="input tall"></div></div>
    <div class="field" style="left:249px;top:472px"><label>Employee Signature :</label><div class="input tall"></div></div>
    <div class="field" style="left:468px;top:472px"><label>Sign Date :</label><div class="input tall"></div></div>
  </main>

  <footer class="site-footer">Copyright &nbsp;© &nbsp;2016 &nbsp;Company name. &nbsp;All rights reserved.</footer>
</body>
</html>
```